Business Cards for new orthopaedic surgery practice

My husband and I are starting our own orthopaedic surgery practice. We are looking for a business card that is uniform, but one will have my name/title and the other will have his. You can just create one design with my name on it for now. But when I choose your design as the winning design I will ask that you add another copy with his name/title.

We are looking for classy, simple, elite all in one. We like dark blues/a little gold/yellow. Something that goes with our logo. We want our logo incorporated. Here is all the info you need:
Business name: RV Bone & Vitality Center
Location: 38517 North Willowmere Ave
Maple Harbor, FL 33990
Phone: 954-218-4063
Fax: 954-582-7341
Email: info@myrvbonecare.example

Names: Lydia Vance, M.D.
Board Certified Hand and Upper Extremity Surgeon

Ebo Dansu, M.D.
Board Certified Hip & Knee Replacement/General Orthopaedic Surgeon

Can decide what you want to put on the back. Maybe a slogan:
Grounded in Care. Centered on You

I am just going to upload our logo. The only thing is if we select you as the winning design, the location, and phone numbers may change. We will need your help to update that once fully solidified.

Industry/Entity Type

Medical

Contact Information for Business Card

Colors
0054AA
0677BA
7BADD7
CADEEF
E8F1F8
0094D4
00A9DD
6FCCEA
C7EBF8
E9F6FB

Requirements
Must have
• class, appeal,
Should not have
• We want to air on the side of masculine if we are looking at masculine vs. feminine feel. But we still want it classy, sophisticated, and something we will love

```html
<!DOCTYPE html>
<html lang="en">
<head>
<meta charset="utf-8">
<title>RV Bone &amp; Vitality Center — Business Cards</title>
<link href="https://fonts.googleapis.com/css2?family=Poppins:ital,wght@0,400;0,500;0,600;1,300&display=swap" rel="stylesheet">
<style>
  :root {
    --navy: #1b2750;
    --gold: #c9a45c;
    --white: #ffffff;
    --paper: #fbfbfc;
    --ink: #1e2433;
    --rule: #6b6f7a;
    --backdrop: #e9ebef;
  }
  * { box-sizing: border-box; margin: 0; padding: 0; }
  html, body { width: 1200px; height: 900px; overflow: hidden; }
  body {
    background: var(--backdrop);
    font-family: "Poppins", sans-serif;
    position: relative;
  }
  .card {
    position: absolute;
    width: 700px;
    height: 400px;
    border-radius: 26px;
    overflow: hidden;
    box-shadow: 0 10px 30px rgba(20, 28, 50, 0.18);
  }

  /* Front */
  .card-front { left: 250px; top: 40px; background: var(--navy); }
  .front-mark {
    position: absolute; left: 230px; top: 55px;
    width: 240px; height: 240px;
  }
  .mark-name {
    position: absolute; inset: 0;
    display: flex; align-items: center; justify-content: center;
    text-align: center;
    font-weight: 500; font-size: 24px; line-height: 1.3;
    letter-spacing: 0.04em;
  }
  .front-mark .mark-name { color: var(--white); }
  .slogan {
    position: absolute; left: 0; right: 0; top: 322px;
    text-align: center; color: var(--white);
    font-style: italic; font-weight: 300; font-size: 17px;
    letter-spacing: 0.03em;
  }

  /* Back */
  .card-back { left: 250px; top: 470px; background: var(--paper); }
  .back-art { position: absolute; inset: 0; }
  .doctor { position: absolute; left: 40px; }
  .doctor-name { color: var(--gold); font-weight: 600; font-size: 24px; line-height: 1.1; }
  .doctor-title { color: var(--white); font-size: 13.5px; line-height: 1.3; margin-top: 3px; }
  .doctor-one { top: 50px; }
  .doctor-two { top: 130px; }
  .doctor-rule {
    position: absolute; left: 40px; top: 123px; width: 250px; height: 1px;
    background: var(--gold);
  }
  .back-mark {
    position: absolute; left: 478px; top: 70px; width: 210px; height: 210px;
  }
  .back-mark .mark-name { color: var(--navy); font-size: 21px; }
  .address { position: absolute; left: 40px; top: 232px; color: var(--ink); font-size: 14px; line-height: 1.35; }
  .contact-list { position: absolute; left: 40px; top: 282px; list-style: none; color: var(--ink); font-size: 14px; line-height: 1.45; }
  .contact-list li { display: flex; align-items: center; gap: 8px; }
  .contact-list svg { width: 12px; height: 12px; fill: var(--gold); flex: none; }
  .contact-list .web { padding-left: 20px; }
  .appointment { position: absolute; left: 380px; top: 294px; width: 290px; }
  .appointment-title { color: var(--navy); font-weight: 600; font-size: 16px; text-align: center; letter-spacing: 0.02em; }
  .appointment-line { height: 1px; background: var(--rule); margin-top: 12px; }
  .appointment-fields { display: flex; gap: 14px; margin-top: 22px; font-size: 14px; color: var(--ink); }
  .field { flex: 1; display: flex; align-items: flex-end; gap: 8px; }
  .field span { flex: 1; height: 1px; background: var(--rule); margin-bottom: 4px; }
</style>
</head>
<body>

<section class="card card-front" aria-label="Business card front">
  <div class="front-mark">
    <svg width="240" height="240" viewBox="0 0 240 240" aria-hidden="true">
      <circle cx="120" cy="120" r="112" fill="none" stroke="var(--gold)" stroke-width="2"/>
    </svg>
    <p class="mark-name">RV Bone &amp;<br>Vitality Center</p>
  </div>
  <p class="slogan">Grounded in Care. Centered on You</p>
</section>

<section class="card card-back" aria-label="Business card back">
  <svg class="back-art" width="700" height="400" viewBox="0 0 700 400" aria-hidden="true">
    <path d="M0 36 H700 V215 H0 Z" fill="var(--navy)"/>
    <circle cx="583" cy="175" r="118" fill="var(--paper)"/>
  </svg>

  <div class="doctor doctor-one">
    <h1 class="doctor-name">Lydia Vance, M.D.</h1>
    <p class="doctor-title">Board Certified Hand and<br>Upper Extremity Surgeon</p>
  </div>
  <div class="doctor-rule"></div>
  <div class="doctor doctor-two">
    <h2 class="doctor-name">Ebo Dansu, M.D.</h2>
    <p class="doctor-title">Board Certified Hip &amp; Knee<br>Replacement/General Orthopaedic Surgeon</p>
  </div>

  <div class="back-mark">
    <svg width="210" height="210" viewBox="0 0 210 210" aria-hidden="true">
      <circle cx="105" cy="105" r="98" fill="none" stroke="var(--gold)" stroke-width="2"/>
    </svg>
    <p class="mark-name">RV Bone &amp;<br>Vitality Center</p>
  </div>

  <p class="address">38517 North Willowmere Ave<br>Maple Harbor, FL 33990</p>
  <ul class="contact-list">
    <li><svg viewBox="0 0 12 12"><path d="M2.5 1 L4.5 1 L5.3 3.4 L4 4.4 C4.6 5.8 6.2 7.4 7.6 8 L8.6 6.7 L11 7.5 L11 9.5 C11 10.4 10.3 11 9.5 11 C5 11 1 7 1 2.5 C1 1.7 1.6 1 2.5 1 Z"/></svg>954-218-4063</li>
    <li><svg viewBox="0 0 12 12"><path d="M3 1 H8 V4 H3 Z M1 5 H11 V10 H1 Z"/></svg>954-582-7341</li>
    <li><svg viewBox="0 0 12 12"><path d="M1 2.5 H11 V9.5 H1 Z" fill="none" stroke="var(--gold)" stroke-width="1.2"/><path d="M1 2.5 L6 6.5 L11 2.5" fill="none" stroke="var(--gold)" stroke-width="1.2"/></svg>info@myrvbonecare.example</li>
    <li class="web">www.rvbonevitality.example</li>
  </ul>

  <div class="appointment">
    <p class="appointment-title">NEXT APPOINTMENT</p>
    <div class="appointment-line"></div>
    <div class="appointment-fields">
      <div class="field">Date <span></span></div>
      <div class="field">Time <span></span></div>
    </div>
  </div>
</section>

</body>
</html>
```